Veltrane Group Business Card Design

The CEO is looking for a new trendy look for his business card.
You can stay with current branding or come up with something new/creative. It can be 3D, including Medical Office buildings. You can use our logo in a variety of colors. Please include name, title, company name, company website, email address, cell number

Target Market(s)

Real Estate Development and Construction

Industry/Entity Type

Health care real estate

Contact Information for Business Card

Rohesh Kamdar, CEO M-604.781.2249 E-roheshkamdar@veltrane.com Address:4180 Lindqvist Ave, Tampa, FL 33482 www.veltrane.com

Font styles to use
Other font styles liked:
• Be creative

Requirements
Must have
• Creative, trendy look
Nice to have
• Please go to our website to get a feel- www. veltrane.com
Should not have
• small fonts

```html
<!DOCTYPE html>
<html lang="en">
<head>
<meta charset="utf-8">
<title>Veltrane Group Business Card</title>
<link rel="stylesheet" href="https://fonts.googleapis.com/css2?family=Montserrat:wght@400;600;800&display=swap">
<style>
  :root {
    --backdrop: #c8bfa9;
    --paper: #ffffff;
    --brand-red: #b01e28;
    --brand-navy: #1d3352;
    --ink: #2b2b2b;
  }
  * { box-sizing: border-box; margin: 0; padding: 0; }
  html, body {
    width: 1116px;
    height: 1200px;
    overflow: hidden;
    background: var(--backdrop);
    font-family: "Montserrat", Arial, sans-serif;
  }
  .card {
    position: absolute;
    background: var(--paper);
    width: 684px;
    height: 390px;
    overflow: hidden;
  }
  .card--front { left: 217px; top: 184px; }
  .card--back { left: 216px; top: 625px; }

  .wordmark {
    position: absolute;
    color: var(--brand-red);
    font-weight: 800;
    text-align: right;
    line-height: 0.98;
    letter-spacing: -0.02em;
  }
  .card--front .wordmark {
    right: 392px;
    top: 137px;
    font-size: 44px;
  }
  .card--back .wordmark {
    right: 70px;
    top: 92px;
    font-size: 100px;
  }

  .divider {
    position: absolute;
    left: 316px;
    top: 117px;
    width: 2px;
    height: 155px;
    background: var(--brand-red);
  }
  .contact {
    position: absolute;
    left: 338px;
    top: 116px;
    right: 16px;
  }
  .contact__name {
    color: var(--brand-red);
    font-weight: 600;
    font-size: 28px;
    letter-spacing: 0.01em;
    line-height: 1.1;
    white-space: nowrap;
  }
  .contact__title {
    color: var(--ink);
    font-size: 20px;
    line-height: 1.2;
    margin-top: 2px;
  }
  .contact__list {
    list-style: none;
    margin-top: 14px;
  }
  .contact__item {
    display: flex;
    align-items: center;
    gap: 8px;
    color: var(--ink);
    font-size: 20px;
    line-height: 30px;
    white-space: nowrap;
  }
  .contact__icon { width: 14px; height: 14px; flex: none; }

  .address-band {
    position: absolute;
    left: 0;
    right: 0;
    bottom: 0;
    height: 58px;
    border-top: 4px solid var(--brand-red);
  }
  .address-band__inner {
    position: absolute;
    left: 0;
    right: 0;
    top: 3px;
    bottom: 0;
    background: var(--brand-navy);
    color: #fff;
    font-size: 21px;
    display: flex;
    justify-content: center;
    align-items: center;
    padding-bottom: 14px;
  }
</style>
</head>
<body>
  <section class="card card--front">
    <div class="wordmark">Veltrane<br>Group</div>
    <div class="divider"></div>
    <div class="contact">
      <div class="contact__name">ROHESH KAMDAR</div>
      <div class="contact__title">CEO</div>
      <ul class="contact__list">
        <li class="contact__item">
          <svg class="contact__icon" viewBox="0 0 14 14" aria-hidden="true"><rect x="3" y="0.5" width="8" height="13" rx="1.5" fill="none" stroke="#b01e28" stroke-width="1.6"/><circle cx="7" cy="11" r="0.9" fill="#b01e28"/></svg>
          604.781.2249
        </li>
        <li class="contact__item">
          <svg class="contact__icon" viewBox="0 0 14 14" aria-hidden="true"><rect x="0.5" y="3" width="13" height="9" fill="#b01e28"/><path d="M0.5 3 L7 8 L13.5 3" fill="none" stroke="#fff" stroke-width="1.2"/></svg>
          roheshkamdar@veltrane.com
        </li>
        <li class="contact__item">
          <svg class="contact__icon" viewBox="0 0 14 14" aria-hidden="true"><circle cx="7" cy="7" r="6.5" fill="#b01e28"/><ellipse cx="7" cy="7" rx="2.6" ry="6.5" fill="none" stroke="#fff" stroke-width="1"/><line x1="0.5" y1="7" x2="13.5" y2="7" stroke="#fff" stroke-width="1"/></svg>
          www.veltrane.com
        </li>
      </ul>
    </div>
    <div class="address-band">
      <div class="address-band__inner">4180 Lindqvist Ave, Tampa, FL 33482</div>
    </div>
  </section>

  <section class="card card--back">
    <div class="wordmark">Veltrane<br>Group</div>
  </section>
</body>
</html>
```